Velvet Circle club

We are looking to redesign the user interface of our mobile app “Velvet Circle”, which is the official rewards program for our luxury casino brand, Kestrane Harbour.
Our goal is to give the app a more elegant, premium, and user-friendly design that reflects the exclusivity of our brand and the luxury experience we offer our VIP clientele.
What We Need:
A complete UI design for the app’s main screens, including:
Splash Screen
01 Login / Signup Screen
02 Home Dashboard
Buttons -
Home / my card / my wallet / my booking / my host
My wallet / my offer / lucky game / my taxi / entertainment / online
03 Profile screen
04 My wallet
05 My offer
06Packages
07 My booking
08 My host
09 My card
we attached our privies app all the screen for you reference
Inspiration:
Think of luxury brands like Dunmore-Vale, Corvix Onyx, or high-end lifestyle apps. Clean interfaces, classy animations, and a sense of exclusivity are key.
We’re excited to see fresh, innovative takes that elevate the app to a truly world-class luxury experience for our users.
Thank you!
Casino

```html
<!DOCTYPE html>
<html lang="en">
<head>
<meta charset="utf-8">
<title>Velvet Circle club – App Screens</title>
<link rel="stylesheet" href="https://fonts.googleapis.com/css2?family=Outfit:wght@300;400;500;600&display=swap">
<style>
  :root{
    --bg-canvas:#ffffff;
    --screen:#242424;
    --panel:#2b2b2b;
    --tile:#2e2e2e;
    --gold:#f0a531;
    --gold-deep:#e8961f;
    --ring:#d9542f;
    --text:#f1f1f1;
    --muted:#cfcfcf;
    --red:#e3342f;
    --line:#444444;
  }
  *{box-sizing:border-box;margin:0;padding:0}
  html,body{width:1200px;height:785px;overflow:hidden;background:var(--bg-canvas);font-family:"Outfit",sans-serif;color:var(--text)}
  .canvas{position:relative;width:1200px;height:785px}
  .screen{position:absolute;top:58px;width:306px;height:662px;background:var(--screen);border-radius:34px;overflow:hidden}
  .screen--home{left:66px}
  .screen--login{left:444px}
  .screen--redeem{left:821px}

  .header{position:absolute;top:22px;left:0;right:0;height:60px}
  .round-btn{position:absolute;top:14px;width:32px;height:32px;border-radius:50%;background:#1e1e1e;border:1px solid #3a3a3a;display:flex;align-items:center;justify-content:center}
  .round-btn--left{left:28px}
  .round-btn--right{right:28px}
  .brand{position:absolute;left:0;right:0;top:14px;text-align:center;display:flex;flex-direction:column;align-items:center;gap:4px}
  .brand__dot{width:12px;height:12px;border-radius:50%;background:var(--red)}
  .brand__name{font-size:16px;font-weight:600;color:var(--gold);letter-spacing:.5px}

  /* home */
  .banner{position:absolute;top:108px;left:22px;width:262px;height:175px;background:linear-gradient(135deg,#2a3c8f 0%,#6a4aa8 45%,#c89a3a 100%)}
  .grid{position:absolute;top:300px;left:30px;width:246px;display:grid;grid-template-columns:1fr 1fr;gap:12px}
  .tile{height:94px;background:var(--tile);border-radius:12px;display:flex;flex-direction:column;align-items:center;justify-content:center;gap:12px}
  .tile__icon{width:40px;height:40px;border-radius:50%;border:1.5px solid var(--ring);display:flex;align-items:center;justify-content:center}
  .tile__label{font-size:11px;font-weight:500;letter-spacing:.3px}

  .nav{position:absolute;bottom:0;left:0;right:0;height:40px;background:var(--gold);display:flex;justify-content:space-around;align-items:center;padding:0 12px}

  /* login */
  .login-card{position:absolute;top:104px;left:14px;right:14px;bottom:0;background:var(--panel);border-radius:18px 18px 0 0;text-align:center}
  .section-title{display:flex;align-items:center;justify-content:center;gap:10px;font-size:15px;font-weight:500}
  .section-title svg{flex:none}
  .login-card p{font-size:12.5px;font-weight:300;line-height:30px;color:var(--text)}
  .pill{display:inline-flex;align-items:center;gap:9px;height:34px;padding:0 18px;border:1px solid var(--gold);border-radius:18px;font-size:12px;color:var(--text)}
  .divider{height:1px;background:var(--line);margin:0 10px}
  .or{color:var(--red);font-size:12px;font-weight:500}

  /* redeem */
  .redeem-card{position:absolute;top:92px;left:14px;right:14px;bottom:0;background:var(--panel);border-radius:18px 18px 0 0}
  .redeem-title{text-align:center;font-size:15px;font-weight:500;margin-top:26px}
  .redeem-sub{text-align:center;font-size:11px;font-weight:500;color:var(--gold);margin-top:18px}
  .steps{position:absolute;top:120px;left:18px;right:14px}
  .steps__rail{position:absolute;left:14px;top:16px;height:380px;border-left:1px dashed var(--gold)}
  .step{position:relative;display:flex;align-items:center;gap:16px;padding-right:6px}
  .step__num{flex:none;width:29px;height:29px;background:var(--gold);border-radius:5px;font-size:13px;font-weight:600;display:flex;align-items:center;justify-content:center;color:#fff;z-index:1}
  .step__text{font-size:10.5px;line-height:20px;font-weight:300}
  .step-sep{height:1px;background:var(--line);margin-left:46px}
</style>
</head>
<body>
<div class="canvas">

  <!-- Home dashboard -->
  <section class="screen screen--home">
    <div class="header">
      <div class="round-btn round-btn--left"><svg width="12" height="10" viewBox="0 0 12 10"><path d="M0 1h12M0 5h12M0 9h12" stroke="#fff" stroke-width="1.6"/></svg></div>
      <div class="brand"><span class="brand__dot"></span><span class="brand__name">VELVET CIRCLE</span></div>
      <div class="round-btn round-btn--right"><svg width="12" height="13" viewBox="0 0 12 13"><path d="M6 1c2.5 0 4 2 4 4.5V9l1.5 1.5H.5L2 9V5.5C2 3 3.5 1 6 1z" fill="#fff"/><circle cx="6" cy="11.8" r="1.2" fill="#fff"/></svg></div>
    </div>
    <div class="banner" role="img" aria-label="Festive event promotion banner with guests in evening wear"></div>
    <div class="grid">
      <div class="tile"><div class="tile__icon"><svg width="18" height="16" viewBox="0 0 18 16" fill="none" stroke="#f0a531" stroke-width="1.3"><rect x="1" y="3" width="16" height="12" rx="2"/><path d="M12 8h5v4h-5z"/><path d="M3 3l9-2 1 2"/></svg></div><span class="tile__label">MY WALLET</span></div>
      <div class="tile"><div class="tile__icon"><svg width="20" height="20" viewBox="0 0 20 20" fill="none" stroke="#f0a531" stroke-width="1.3"><circle cx="10" cy="10" r="8"/><path d="M7 13l6-6"/><circle cx="7.5" cy="7.5" r="1"/><circle cx="12.5" cy="12.5" r="1"/></svg></div><span class="tile__label">MY OFFER</span></div>
      <div class="tile"><div class="tile__icon"><svg width="20" height="20" viewBox="0 0 20 20" fill="none" stroke="#f0a531" stroke-width="1.3"><circle cx="10" cy="10" r="8"/><circle cx="10" cy="10" r="4"/><circle cx="10" cy="10" r="1.3"/><path d="M10 2v4M10 14v4M2 10h4M14 10h4"/></svg></div><span class="tile__label">LUCKY GAME</span></div>
      <div class="tile"><div class="tile__icon"><svg width="20" height="18" viewBox="0 0 20 18" fill="none" stroke="#f0a531" stroke-width="1.3"><rect x="7" y="1" width="6" height="3"/><path d="M4 9l2-5h8l2 5"/><rect x="2" y="9" width="16" height="5" rx="1.5"/><path d="M4 14v3M16 14v3"/><circle cx="5.5" cy="11.5" r="1"/><circle cx="14.5" cy="11.5" r="1"/></svg></div><span class="tile__label">MY TAXI</span></div>
      <div class="tile"><div class="tile__icon"><svg width="20" height="20" viewBox="0 0 20 20" fill="none" stroke="#f0a531" stroke-width="1.3"><circle cx="6" cy="8" r="2"/><circle cx="14" cy="8" r="2"/><circle cx="10" cy="10" r="2"/><path d="M3 17v-3a3 3 0 016 0M11 17v-3a3 3 0 016 0M7 18v-2a3 3 0 016 0v2M4 2l1 2M10 1v3M16 2l-1 2"/></svg></div><span class="tile__label">ENTERTAINMENT</span></div>
      <div class="tile"><div class="tile__icon"><svg width="20" height="18" viewBox="0 0 20 18" fill="none" stroke="#f0a531" stroke-width="1.3"><rect x="1" y="1" width="15" height="11" rx="1"/><path d="M4 4h4v3H4zM10 4h3M10 7h3M6 15h6"/><path d="M13 10l5 2-2 1 2 3-1 1-2-3-1 2z"/></svg></div><span class="tile__label">ONLINE</span></div>
    </div>
    <nav class="nav">
      <svg width="14" height="14" viewBox="0 0 14 14"><path d="M7 1l6 6h-2v6H8V9H6v4H3V7H1z" fill="#fff"/></svg>
      <svg width="16" height="14" viewBox="0 0 16 14"><rect x="1" y="4" width="14" height="9" rx="1" fill="#fff"/><rect x="5" y="1" width="6" height="3" fill="#fff"/></svg>
      <svg width="16" height="14" viewBox="0 0 16 14"><rect x="1" y="3" width="14" height="10" rx="1.5" fill="#fff"/><rect x="10" y="6" width="5" height="4" fill="#f0a531"/></svg>
      <svg width="15" height="14" viewBox="0 0 15 14"><rect x="1" y="2" width="13" height="11" rx="1" fill="#fff"/><path d="M5 8l2 2 3-4" stroke="#f0a531" stroke-width="1.4" fill="none"/></svg>
      <svg width="16" height="14" viewBox="0 0 16 14"><circle cx="6" cy="4" r="3" fill="#fff"/><path d="M1 13a5 5 0 0110 0z" fill="#fff"/><path d="M12 6h3M12 9h3M12 12h3" stroke="#fff" stroke-width="1.3"/></svg>
    </nav>
  </section>

  <!-- Login / Signup -->
  <section class="screen screen--login">
    <div class="header">
      <div class="brand"><span class="brand__dot"></span><span class="brand__name">VELVET CIRCLE</span></div>
    </div>
    <div class="login-card">
      <div class="section-title" style="margin-top:34px"><svg width="17" height="17" viewBox="0 0 17 17" fill="none" stroke="#f0a531" stroke-width="1.3"><circle cx="8.5" cy="8.5" r="7.5"/><circle cx="8.5" cy="6.5" r="2.6"/><path d="M3.6 14a5.5 5.5 0 019.8 0"/></svg>MEMBER LOGIN</div>
      <p style="margin-top:14px">Now you can enjoy all the<br>excitement of the casino right at<br>your fingertips.</p>
      <div style="margin-top:22px"><span class="pill"><svg width="13" height="12" viewBox="0 0 13 12"><circle cx="5" cy="3.5" r="3" fill="#fff"/><path d="M0 12a5 5 0 0110 0z" fill="#fff"/></svg>SIGN IN</span></div>
      <div class="divider" style="margin-top:32px"></div>
      <div class="section-title" style="margin-top:34px"><svg width="17" height="17" viewBox="0 0 17 17" fill="none" stroke="#f0a531" stroke-width="1.3"><circle cx="8.5" cy="8.5" r="7.5"/><circle cx="8.5" cy="6.5" r="2.6"/><path d="M3.6 14a5.5 5.5 0 019.8 0"/></svg>NEW MEMBER LOGIN</div>
      <p style="margin-top:12px">If you are a first time user, please go<br>through the sign up process.</p>
      <div style="margin-top:20px"><span class="pill"><svg width="13" height="12" viewBox="0 0 13 12"><circle cx="5" cy="3.5" r="3" fill="#fff"/><path d="M0 12a5 5 0 0110 0z" fill="#fff"/></svg>SIGN UP</span></div>
      <div class="or" style="margin-top:16px">OR</div>
      <p style="margin-top:6px">If you are with a temporary ID, sign in here</p>
      <div style="margin-top:12px"><span class="pill" style="padding:0 20px"><svg width="13" height="12" viewBox="0 0 13 12"><circle cx="5" cy="3.5" r="3" fill="#fff"/><path d="M0 12a5 5 0 0110 0z" fill="#fff"/></svg>TEMPORARY SIGN IN</span></div>
    </div>
  </section>

  <!-- How to redeem -->
  <section class="screen screen--redeem">
    <div class="header" style="top:12px">
      <div class="round-btn round-btn--left"><svg width="12" height="10" viewBox="0 0 12 10"><path d="M0 1h12M0 5h12M0 9h12" stroke="#fff" stroke-width="1.6"/></svg></div>
      <div class="brand" style="top:6px"><span class="brand__dot"></span><span class="brand__name">VELVET CIRCLE</span></div>
      <div class="round-btn round-btn--right"><svg width="12" height="13" viewBox="0 0 12 13"><path d="M6 1c2.5 0 4 2 4 4.5V9l1.5 1.5H.5L2 9V5.5C2 3 3.5 1 6 1z" fill="#fff"/><circle cx="6" cy="11.8" r="1.2" fill="#fff"/></svg></div>
    </div>
    <div class="redeem-card">
      <h2 class="redeem-title">HOW TO REDEEM</h2>
      <h3 class="redeem-sub">HOW TO REDEEM YOUR VOUCHERS</h3>
      <div class="steps" style="top:106px">
        <div class="steps__rail"></div>
        <div class="step"><span class="step__num">01</span><span class="step__text">Select the preferred Partner you want to redeem your voucher at</span></div>
        <div class="step-sep" style="margin-top:18px"></div>
        <div class="step" style="margin-top:20px"><span class="step__num">02</span><span class="step__text">Present your kestrane voucher at time of payment by showing the voucher and number appearing on your mobile</span></div>
        <div class="step-sep" style="margin-top:20px"></div>
        <div class="step" style="margin-top:22px"><span class="step__num">03</span><span class="step__text">Indicate the number and value of the voucher you want to pay with</span></div>
        <div class="step-sep" style="margin-top:20px"></div>
        <div class="step" style="margin-top:22px"><span class="step__num">04</span><span class="step__text">You will receive a message to your app indicating a successful transaction</span></div>
        <div class="step-sep" style="margin-top:20px"></div>
        <div class="step" style="margin-top:22px"><span class="step__num">05</span><span class="step__text">The transaction voucher will get deleted from your Voucher</span></div>
      </div>
    </div>
    <nav class="nav">
      <svg width="14" height="14" viewBox="0 0 14 14"><path d="M7 1l6 6h-2v6H8V9H6v4H3V7H1z" fill="#fff"/></svg>
      <svg width="16" height="14" viewBox="0 0 16 14"><rect x="1" y="4" width="14" height="9" rx="1" fill="#fff"/><rect x="5" y="1" width="6" height="3" fill="#fff"/></svg>
      <svg width="16" height="14" viewBox="0 0 16 14"><rect x="1" y="3" width="14" height="10" rx="1.5" fill="#fff"/><rect x="10" y="6" width="5" height="4" fill="#f0a531"/></svg>
      <svg width="15" height="14" viewBox="0 0 15 14"><rect x="1" y="2" width="13" height="11" rx="1" fill="#fff"/><path d="M5 8l2 2 3-4" stroke="#f0a531" stroke-width="1.4" fill="none"/></svg>
      <svg width="16" height="14" viewBox="0 0 16 14"><circle cx="6" cy="4" r="3" fill="#fff"/><path d="M1 13a5 5 0 0110 0z" fill="#fff"/><path d="M12 6h3M12 9h3M12 12h3" stroke="#fff" stroke-width="1.3"/></svg>
    </nav>
  </section>

</div>
</body>
</html>
```